Hop Bright Meadow Business Website Branding

Looking for a wordpress template design with CSS and HTML encoding. Current website can be seen at hopbrightmeadow.example.

WE ARE CURRENTLY IN PROCESS GETTING A LOGO DESIGN... I HAVE INCLUDED THE TOP POTENTIAL DESIGNS FOR REFERENCE TO HELP UNDERSTAND WHAT STYLE WE ARE LOOKING FOR...
NOTE: THE “PEBBLE CREW” LOGO WAS A PREVIOUS COMPANY WE OWNED SO YOU CAN GE A FEEL FOR THE TYPE OF DESIGNS WE HAVE USED IN THE PAST.

My blog will focus on making a connection with wild Florida, it’s wildlife, plants and animals... with an eye toward Florida conservation, nature adventure trips, and education... Content, photos and other merchandise will also be offered for sale.
I’m looking for a site design that incorporates Florida nature and wildlife/plants, with a fun “Old Florida” retro-adventure feel.
When they see this site it should speak to the import of natural Florida and the critical nature of the ecosystem here... while being instantly recognizable and iconic... IE: when I think of florida I think of water, plants, warmth, sunsets etc...

https://join.chatroomhub.example/t/lumexstudio-kzt4821/shared_invite/zt-pqwrt83m-hRnLvXaKoPzsYcB1Uq7JdM

Target Market(s)

Nature, Education, Conservation, Photography

Industry/Entity Type

Photographer

Coding

Coded - Design and coding required

Requirements
Must have
• Need to have site wide template design which generally includes a landing page and a general page template for other pages... Must include html and css encoding...
Should not have
• Any animals included in the site should be Florida native... IE: no African animals etc... This will require some research to ensure that if animals are included that they are part of the Florida ecosystem.

```html
<!DOCTYPE html>
<html lang="en">
<head>
<meta charset="utf-8">
<title>Hop Bright Meadow</title>
<link rel="stylesheet" href="https://fonts.googleapis.com/css2?family=Roboto+Slab:wght@400;700&family=Lato:wght@300;400;700&display=swap">
<style>
:root{
  --peach:#f6d8b4;
  --orange:#d9773a;
  --night:#2b1e21;
  --ink:#3a2a28;
  --muted:#8a6f62;
  --white:#ffffff;
}
*{box-sizing:border-box;margin:0;padding:0}
html,body{width:1200px;height:4478px;overflow:hidden}
body{background:var(--peach);font-family:"Lato",sans-serif;color:var(--ink);position:relative}
.abs{position:absolute}

/* nav */
.site-nav{top:0;left:0;width:1200px;height:104px;background:var(--peach);z-index:5}
.nav-link{position:absolute;top:54px;font-family:"Roboto Slab",serif;font-size:15px;color:var(--ink);letter-spacing:.3px;white-space:nowrap}
.nav-link.active::after{content:"";position:absolute;left:8px;right:8px;top:26px;height:2px;background:var(--ink)}
.brand-disc{left:470px;top:-52px;width:260px;height:262px;border-radius:50%;background:var(--peach);z-index:6}
.brand-mark{left:578px;top:26px;width:44px;height:44px;border-radius:50%;background:var(--ink);z-index:7}
.brand-name{left:470px;top:112px;width:260px;text-align:center;font-family:"Roboto Slab",serif;font-weight:700;font-size:21px;line-height:26px;color:var(--ink);z-index:7}

/* hero */
.hero{top:104px;left:0;width:1200px;height:760px;background:linear-gradient(180deg,#2f5d7c 0%,#c26a3f 18%,#f49a32 25%,#6c6d78 34%,#3f5f72 48%,#8fa7ad 62%,#6a4a34 80%,#4a3324 100%)}
.hero-title{top:382px;left:0;width:1200px;text-align:center;font-family:"Roboto Slab",serif;font-weight:700;font-size:40px;line-height:60px;color:var(--white);text-shadow:0 2px 6px rgba(0,0,0,.45)}
.btn-dark{top:514px;left:523px;width:154px;height:52px;border-radius:26px;background:var(--night);color:var(--white);font-size:14px;font-weight:700;line-height:52px;text-align:center}
.hero-edge{top:740px;left:0;width:1200px;height:130px}

/* section headings */
.heading{font-family:"Roboto Slab",serif;font-size:34px;font-weight:400;color:var(--ink);white-space:nowrap}
.heading b{font-weight:700}
.rule{height:3px;width:104px;background:var(--orange)}
.body-text{font-size:14px;line-height:34.5px;color:var(--muted)}
.btn-orange{height:52px;border-radius:26px;background:var(--orange);color:var(--white);font-size:14px;font-weight:700;line-height:52px;text-align:center;box-shadow:0 3px 6px rgba(0,0,0,.18)}
.photo-round{border-radius:50%;box-shadow:-6px -4px 0 var(--orange),0 8px 14px rgba(0,0,0,.25)}

/* wonders */
.wonders{top:1496px;left:0;width:1200px;height:812px;background:var(--night)}
.tile{width:316px;height:254px;border:3px solid var(--white)}

/* testimonials */
.testimonials{top:2922px;left:0;width:1200px;height:361px;background:linear-gradient(90deg,#2c3322,#4a4a3a 50%,#2e3424)}
.quote{font-style:italic;font-family:"Roboto Slab",serif;font-size:17px;line-height:35px;color:var(--white);text-align:center;width:1200px;left:0}

/* blogs */
.blog-img{width:318px;height:256px;border-radius:4px}
.blog-date{font-size:14px;color:var(--ink)}
.blog-title{font-size:13px;font-weight:700;line-height:28px;color:var(--ink);letter-spacing:.3px;width:318px}

/* footer */
.footer{top:3904px;left:0;width:1200px;height:574px}
.foot-link{position:absolute;top:4158px;font-family:"Roboto Slab",serif;font-size:15px;color:var(--white);white-space:nowrap}
.foot-line{left:110px;width:980px;height:1px;background:rgba(255,255,255,.35)}
.foot-icon{width:56px;height:56px;border-radius:50%;border:2px solid var(--white)}
.foot-text{font-size:15px;color:var(--white);text-align:center;line-height:34px}
</style>
</head>
<body>

<header class="abs site-nav">
  <span class="nav-link active" style="left:110px">HOME</span>
  <span class="nav-link" style="left:197px">ABOUT</span>
  <span class="nav-link" style="left:290px">GALLER</span>
  <span class="nav-link" style="left:392px">BLOGS</span>
  <span class="nav-link" style="left:752px">TESTIMONIALS</span>
  <span class="nav-link" style="left:909px">CONTACT</span>
  <span class="nav-link" style="left:1021px">
    <svg width="13" height="13" viewBox="0 0 13 13" style="vertical-align:-1px"><circle cx="6.5" cy="4" r="3" fill="#3a2a28"/><path d="M1 13c0-4 2.5-5.5 5.5-5.5S12 9 12 13z" fill="#3a2a28"/></svg> LOGIN</span>
</header>
<div class="abs brand-disc"></div>
<div class="abs brand-mark"></div>
<div class="abs brand-name">HOP BRIGHT<br>MEADOW</div>

<section class="abs hero" role="img" aria-label="Sunset over ocean waves washing onto a sandy Florida beach"></section>
<h1 class="abs hero-title">EXPLORING FLORIDA'S NATURAL<br>WONDERS</h1>
<div class="abs btn-dark">GET STARTED</div>
<svg class="abs hero-edge" viewBox="0 0 1200 130" preserveAspectRatio="none">
  <path d="M0 60 Q600 0 1200 60 L1200 130 L0 130Z" fill="#f6d8b4"/>
</svg>

<!-- about -->
<div class="abs photo-round" style="left:118px;top:946px;width:442px;height:446px;background:radial-gradient(circle at 65% 55%,#e9a83e,#6a5a2c 40%,#2e2a1c 75%)" role="img" aria-label="Misty pine forest at sunrise"></div>
<h2 class="abs heading" style="left:600px;top:998px">ABOUT <b>HOP BRIGHT MEADOW</b></h2>
<div class="abs rule" style="left:600px;top:1058px"></div>
<p class="abs body-text" style="left:600px;top:1082px;width:490px">Come explore wild places and stunning scenery with me as I discover new and exciting eco-adventures and learn about the rare and unique wildlife and environments that make Florida so precious and extraordinary. I hope you can vicariously enjoy the wild and untamed beauty of Florida through my eyes, and learn some amazing things about nature on our explorations.</p>
<div class="abs btn-orange" style="left:600px;top:1278px;width:154px">READ MORE</div>

<!-- wonders -->
<section class="abs wonders"></section>
<h2 class="abs heading" style="left:0;width:1200px;text-align:center;top:1566px;color:#fff">FLORIDA'S <b>NATURAL WONDERS</b></h2>
<div class="abs rule" style="left:548px;top:1628px"></div>
<div class="abs tile" style="left:110px;top:1697px;background:linear-gradient(160deg,#3f6a3a,#8aa98a 55%,#2e4a3a)" role="img" aria-label="Kayak on a shaded forest river"></div>
<div class="abs tile" style="left:440px;top:1697px;background:linear-gradient(180deg,#6a4a1c,#c9912e 60%,#8a5a1e)" role="img" aria-label="Two egrets wading at golden hour"></div>
<div class="abs tile" style="left:770px;top:1697px;background:linear-gradient(180deg,#3c6a2a,#486030 50%,#8ea09a)" role="img" aria-label="Alligator resting by the water"></div>
<div class="abs tile" style="left:110px;top:1972px;background:linear-gradient(160deg,#4f6a34,#9a8a6a 55%,#3a4a26)" role="img" aria-label="Florida panther among leaves"></div>
<div class="abs tile" style="left:440px;top:1972px;background:linear-gradient(180deg,#2e5a22,#4a4a3e 60%,#2a2a24)" role="img" aria-label="Young animal wading through green water"></div>
<div class="abs tile" style="left:770px;top:1972px;background:linear-gradient(180deg,#2b5c9a,#e9a24a 45%,#1e3550)" role="img" aria-label="Pier at sunset over calm water"></div>

<!-- about me -->
<h2 class="abs heading" style="left:110px;top:2450px;font-weight:700;font-size:38px">ABOUT ME</h2>
<div class="abs rule" style="left:110px;top:2518px"></div>
<p class="abs body-text" style="left:110px;top:2547px;width:470px;line-height:32.5px">Hello nature lovers! I'm Marla Quenby, a wildlife educator, Florida Master Naturalist, nature writer and photographer, busy mama of three kiddos, a playful Havanese puppy, two very chubby guinea pigs, and a giant tree frog. I have a passion for all things nature and I adore living in Southwest Florida. I will always be a California girl.</p>
<div class="abs btn-orange" style="left:110px;top:2733px;width:154px">READ MORE</div>
<div class="abs photo-round" style="left:642px;top:2388px;width:442px;height:446px;background:radial-gradient(circle at 55% 50%,#d9a58a,#8a5a3c 40%,#5a7a8a 75%)" role="img" aria-label="Portrait of the site author at the beach"></div>

<!-- testimonials -->
<section class="abs testimonials" role="img" aria-label="Wooden boardwalk through palmetto scrub"></section>
<h2 class="abs heading" style="left:0;width:1200px;text-align:center;top:2992px;font-weight:700;font-size:40px;color:#fff">TESTIMONIALS</h2>
<div class="abs rule" style="left:548px;top:3058px"></div>
<p class="abs quote" style="top:3089px">Nature has been for me, as long as I remember, a source of solace, inspiration, adventure, and delight;<br>a home, a teacher, a companion</p>
<p class="abs" style="left:0;width:1200px;text-align:center;top:3181px;font-size:16px;color:var(--orange);letter-spacing:.4px">DELIA FARROW</p>

<!-- blogs -->
<h2 class="abs heading" style="left:0;width:1200px;text-align:center;top:3378px;font-weight:700;font-size:40px">LATEST BLOGS</h2>
<div class="abs rule" style="left:548px;top:3452px"></div>
<div class="abs blog-img" style="left:110px;top:3492px;background:linear-gradient(135deg,#3a6a2a,#e64a24 45%,#f2a03a 70%,#4a7a2a)" role="img" aria-label="Red and yellow lily flower"></div>
<div class="abs blog-img" style="left:440px;top:3492px;background:linear-gradient(180deg,#5a7a4a,#3a5a2a 60%,#6a8a4a)" role="img" aria-label="White wildflowers in a forest clearing"></div>
<div class="abs blog-img" style="left:770px;top:3492px;background:linear-gradient(135deg,#3a6a2e,#d9a78e 55%,#c58a70)" role="img" aria-label="Tiny dark frog held on a fingertip"></div>
<p class="abs blog-date" style="left:110px;top:3770px">September 24th-October 22nd, 2020</p>
<p class="abs blog-date" style="left:440px;top:3770px">September 24th-October 22nd, 2020</p>
<p class="abs blog-date" style="left:770px;top:3770px">September 24th-October 22nd, 2020</p>
<p class="abs blog-title" style="left:110px;top:3798px">COMMUNING WITH NATURE AT HERON HOLLOW DOME PRESERVE TRAILS</p>
<p class="abs blog-title" style="left:440px;top:3798px">LOREM IPSUM DOLOR SIT AMET, CONSECTETUR ADIPISCING ELIT</p>
<p class="abs blog-title" style="left:770px;top:3798px">LOREM IPSUM DOLOR SIT AMET, CONSECTETUR ADIPISCING ELIT</p>

<!-- footer -->
<svg class="abs footer" viewBox="0 0 1200 574" preserveAspectRatio="none">
  <path d="M0 60 Q600 -10 1200 60 L1200 574 L0 574Z" fill="#d9773a"/>
</svg>
<span class="foot-link" style="left:300px">HOME</span>
<span class="foot-link" style="left:386px">ABOUT</span>
<span class="foot-link" style="left:477px">GALLERY</span>
<span class="foot-link" style="left:586px">BLOGS</span>
<span class="foot-link" style="left:673px">TESTIMONIALS</span>
<span class="foot-link" style="left:827px">CONTACT</span>
<div class="abs foot-line" style="top:4209px"></div>

<div class="abs foot-icon" style="left:267px;top:4233px">
  <svg width="52" height="52" viewBox="0 0 52 52"><path d="M20 17c1-1 2.5-1 3 0l2 3.5c.5 1 0 2-.8 2.6l-1.3 1c1 2.5 3 4.5 5.5 5.5l1-1.3c.6-.8 1.6-1.3 2.6-.8l3.5 2c1 .5 1 2 0 3l-1.5 1.5c-1.5 1.5-4 1.2-6.5-.3-3.5-2-6.5-5-8.5-8.5-1.5-2.5-1.8-5-.3-6.5z" fill="#fff"/></svg>
</div>
<div class="abs foot-icon" style="left:556px;top:4233px">
  <svg width="52" height="52" viewBox="0 0 52 52"><path d="M26 15a7 7 0 0 1 7 7c0 5-7 13-7 13s-7-8-7-13a7 7 0 0 1 7-7z" fill="#fff"/><circle cx="26" cy="22" r="2.6" fill="#d9773a"/></svg>
</div>
<div class="abs foot-icon" style="left:858px;top:4233px">
  <svg width="52" height="52" viewBox="0 0 52 52"><rect x="16" y="18" width="20" height="15" rx="2" fill="#fff"/><path d="M16.5 19l9.5 7 9.5-7" stroke="#d9773a" stroke-width="1.8" fill="none"/></svg>
</div>
<p class="abs foot-text" style="left:193px;width:200px;top:4303px;font-size:18px">555-010-2480</p>
<p class="abs foot-text" style="left:440px;width:300px;top:4303px;font-size:14px">Lorem ipsum dolor sit amet, consectetur<br>adipiscing elit.Florida</p>
<p class="abs foot-text" style="left:760px;width:260px;top:4303px;font-size:14px">info@hopbrightmeadow.example</p>
<div class="abs foot-line" style="top:4400px"></div>
<p class="abs foot-text" style="left:0;width:1200px;top:4423px;font-size:13px">©2020 All Rights Reserved</p>

</body>
</html>
```